Website for software company "velora"

We need a website for our software company/startup named "velora". We are developing several products (currently 3 standard-software products) which are all in different sectors, but all our products are available for Laptops/PC/Mobile Phones/Tablets, ... We do also create custom software and support our customers with consulting to optimize their processes.
We already have a Logo which you can find in the attached files.
We are a young team of 4 members (two founders and 2 employees).

To get an idea of our products -> the first one is a planning software for healthcare organizations (eg. BlueHaven, firebrigade, pharmacy), the second one is a booking software for sport clubs and the third one is a competition software for sports hunting. You see very diverse. Include or ignore this info of our products as you like.

The design has to be a bootstrap 4 (or higher) design. We have licenced FontAwesome as iconset. Responsive design should come without saying.

• Starting page, product pages, news section, contact, team, services

```html
<!DOCTYPE html>
<html lang="en">
<head>
<meta charset="utf-8">
<title>Velora — Software for every sector</title>
<link rel="stylesheet" href="https://fonts.googleapis.com/css2?family=Montserrat:wght@400;500;600;700;800&family=Open+Sans:wght@400;600;700&display=swap">
<style>
:root{
  --orange:#f26d21;
  --orange-dark:#d95a14;
  --ink:#111111;
  --text:#3d3d3d;
  --muted:#777777;
  --peach:#fdede3;
  --grey-band:#e8e8ea;
  --footer:#1f2127;
  --white:#ffffff;
  --head:"Montserrat",sans-serif;
  --body:"Open Sans",sans-serif;
}
*{box-sizing:border-box;margin:0;padding:0}
html,body{width:1200px;height:4428px;overflow:hidden}
body{font-family:var(--body);color:var(--text);background:var(--white);position:relative}
.abs{position:absolute}
section,header,footer{position:absolute;left:0;width:1200px}
.btn{display:inline-block;background:var(--orange);color:var(--white);font-family:var(--head);font-weight:600;font-size:17px;text-decoration:none;padding:0 24px;line-height:44px;position:relative;box-shadow:6px 6px 0 rgba(242,109,33,.25)}
.btn::after{content:"";position:absolute;right:-14px;top:0;border-left:14px solid var(--orange);border-bottom:44px solid transparent}
.section-title{font-family:var(--head);font-weight:700;color:var(--ink);font-size:42px;text-align:center}
.section-title .caret{display:inline-block;margin-left:14px;border-left:13px solid var(--ink);border-top:11px solid transparent;border-bottom:11px solid transparent;vertical-align:middle}

/* header */
.site-header{top:0;height:86px;background:var(--white);box-shadow:0 2px 6px rgba(0,0,0,.12);z-index:5}
.brand{left:110px;top:20px;font-family:var(--head);font-weight:700;font-size:42px;color:var(--orange);letter-spacing:1px;display:flex;align-items:center;gap:10px}
.brand-dot{width:14px;height:14px;background:var(--orange);display:inline-block}
.main-nav{left:358px;top:33px;display:flex;gap:32px;font-family:var(--head);font-size:15px}
.main-nav a{color:#333;text-decoration:none}
.main-nav a.active{font-weight:700;color:var(--ink)}
.call-btn{left:903px;top:22px;width:178px;height:42px;background:var(--orange);color:var(--white);font-family:var(--head);font-size:15px;display:flex;align-items:center;justify-content:center;gap:8px}
.call-btn::after{content:"";position:absolute;right:-12px;top:0;border-left:12px solid var(--orange);border-bottom:42px solid transparent}

/* hero */
.hero{top:86px;height:610px;overflow:hidden}
.hero-photo{position:absolute;inset:0;background:linear-gradient(100deg,#f3f1ec 0%,#d9d4cc 30%,#8a94a3 60%,#3e5d86 80%,#b9b3ab 100%)}
.hero-copy{left:110px;top:140px}
.hero-copy h1{font-family:var(--head);font-weight:800;font-size:60px;line-height:58px;color:var(--ink)}
.hero-copy p{margin-top:18px;font-size:14px;font-weight:700;color:#222;line-height:23px;width:380px}
.hero-copy .btn{margin-top:20px;font-size:18px}
.hero-cut{left:0;bottom:0;width:1200px;height:120px}

/* about */
.about{top:748px;height:400px}
.about-photo{left:112px;top:0;width:426px;height:387px;background:linear-gradient(120deg,#6d6b66,#b49072 45%,#5c6670)}
.about-body{left:600px;top:0;width:490px}
.about-body h2{font-family:var(--head);font-weight:700;font-size:42px;color:var(--ink)}
.about-body h2 .caret{display:inline-block;margin-left:16px;border-left:13px solid var(--ink);border-top:11px solid transparent;border-bottom:11px solid transparent;vertical-align:middle}
.about-body p{font-size:16px;line-height:27.5px;margin-top:18px;color:#444}
.about-body .btn{margin-top:24px}

/* software */
.software{top:1221px;height:780px}
.software-bg{left:0;top:0;width:1200px;height:780px}
.software .section-title{top:76px;width:100%}
.tabs{top:160px;left:0;width:100%}
.tab{position:absolute;font-family:var(--head);font-weight:500;font-size:18px;color:var(--ink)}
.tab.active{left:181px;top:0;background:var(--orange);color:var(--white);padding:0 18px;line-height:46px}
.tab.active::after{content:"";position:absolute;right:-12px;top:0;border-left:12px solid var(--orange);border-bottom:46px solid transparent}
.product{top:252px;width:300px;height:430px}
.product-photo{position:absolute;left:0;top:0;width:300px;height:212px}
.product-card{position:absolute;left:15px;top:143px;width:270px;height:258px;background:var(--white);clip-path:polygon(0 18px,100% 0,100% 100%,0 100%);text-align:center;padding:48px 22px 0}
.product-card h3{font-family:var(--head);font-weight:600;color:var(--orange);font-size:25px}
.product-card p{font-size:16px;line-height:26px;margin-top:10px;color:#333}
.product .btn{position:absolute;left:73px;top:378px;font-size:17px}

/* testimonials */
.testimonials{top:2060px;height:330px}
.testimonials .section-title{top:20px;width:100%}
.avatar{left:173px;top:142px;width:180px;height:180px;border-radius:50%;border:5px solid var(--orange);background:radial-gradient(circle at 50% 40%,#cfd4d8,#8f959c)}
.quote-mark{left:372px;top:118px;font-family:Georgia,serif;font-size:130px;color:#e2e2e2;line-height:1}
.testimonial-text{left:400px;top:142px;width:690px}
.testimonial-text h4{font-family:var(--head);font-weight:600;font-size:21px;color:var(--ink)}
.testimonial-text p{margin-top:16px;font-size:16px;font-weight:600;line-height:27px;color:#444}
.testimonial-text .who{margin-top:14px;font-family:var(--head);font-weight:700;font-size:18px;color:var(--ink)}
.testimonial-text .who small{font-size:11px;font-weight:600}
.stars{color:#f2a621;font-size:14px;letter-spacing:1px;margin-left:6px}
.arrow{top:185px}

/* news */
.news{top:2468px;height:722px}
.news-bg{left:0;top:0}
.news .section-title{top:52px;width:100%}
.post{top:142px;width:308px;height:476px;background:#efdccf}
.post-photo{position:absolute;left:0;top:0;width:308px;height:226px}
.post-body{position:absolute;left:10px;top:226px;width:288px;height:240px;background:var(--white);padding:22px 26px 0}
.post-meta{font-family:var(--head);font-weight:600;font-size:15px;color:var(--orange)}
.post-body h3{font-family:var(--head);font-weight:600;font-size:18px;line-height:26px;color:#222;margin-top:10px}
.post-body p{font-family:var(--head);font-size:13px;font-weight:500;line-height:21px;color:#666;margin-top:8px}
.post-body a{display:block;margin-top:6px;font-family:var(--head);font-weight:600;font-size:16px;color:var(--orange);text-decoration:none}

/* contact */
.contact{top:3270px;height:660px}
.contact .section-title{top:8px;width:100%}
.contact-lead{top:92px;left:240px;width:720px;text-align:center;font-family:var(--head);font-size:16px;line-height:26px;color:#666}
.info-card{left:113px;top:175px;width:377px;height:462px;background:var(--white);box-shadow:0 2px 14px rgba(0,0,0,.15)}
.info-card h2{font-family:var(--head);font-weight:500;font-size:31px;color:#222;text-align:center;line-height:100px;border-bottom:2px solid #333}
.info-row{position:absolute;left:40px;display:flex;gap:18px}
.info-icon{width:34px;height:34px;border-radius:50%;background:var(--orange);display:flex;align-items:center;justify-content:center;flex:none}
.info-row h4{font-family:var(--head);font-weight:500;font-size:21px;color:#222}
.info-row p{font-family:var(--head);font-size:15px;color:#777;line-height:21px;margin-top:2px}
.message-form{left:545px;top:175px;width:545px;height:463px;background:var(--orange);padding:0 52px 0 32px}
.message-form h2{font-family:var(--head);font-weight:500;font-size:31px;color:var(--white);text-align:center;line-height:100px}
.field{display:block;width:481px;height:64px;background:var(--white);border-radius:6px;border:0;margin-bottom:10px;font-family:var(--head);font-size:15px;color:#666;padding:22px 36px}
.field.tall{height:112px}
.submit{display:block;width:481px;height:64px;background:var(--white);border-radius:6px;margin-top:18px;font-family:var(--head);font-weight:600;font-size:24px;color:var(--orange);text-align:center;line-height:64px;letter-spacing:1px}

/* footer */
.site-footer{top:3955px;height:473px}
.footer-shape{left:0;top:0}
.footer-col{top:170px}
.footer-col h4{font-family:var(--head);font-weight:600;font-size:21px;color:var(--white);margin-bottom:12px}
.footer-col ul{list-style:none}
.footer-col li{font-family:var(--head);font-size:15px;color:#d8d8d8;line-height:27.5px;display:flex;gap:8px;align-items:flex-start}
.footer-col .lead{font-family:var(--head);font-size:13px;color:#cfcfcf;line-height:22px;width:210px;text-align:justify}
.follow{font-family:var(--head);font-size:10px;color:#cfcfcf;margin-top:8px}
.socials{display:flex;gap:18px;margin-top:10px}
.socials span{width:27px;height:27px;border-radius:50%;background:var(--orange)}
.footer-rule{left:110px;top:379px;width:980px;height:1px;background:#666}
.copyright{top:415px;width:100%;text-align:center;font-family:var(--head);font-weight:600;font-size:15px;color:var(--white)}
</style>
</head>
<body>

<header class="site-header">
  <div class="abs brand"><span class="brand-dot"></span>VELORA</div>
  <nav class="abs main-nav">
    <a class="active" href="#">Home</a><a href="#">About</a><a href="#">Our Software</a><a href="#">Latest News</a><a href="#">Contact us</a>
  </nav>
  <div class="abs call-btn">
    <svg width="14" height="14" viewBox="0 0 24 24" fill="#fff"><path d="M6.6 10.8a15 15 0 006.6 6.6l2.2-2.2c.3-.3.7-.4 1-.2 1.1.4 2.3.6 3.6.6.6 0 1 .4 1 1V20c0 .6-.4 1-1 1A17 17 0 013 4c0-.6.4-1 1-1h3.5c.6 0 1 .4 1 1 0 1.3.2 2.5.6 3.6.1.3 0 .7-.2 1z"/></svg>
    +1 555 014 2290
  </div>
</header>

<section class="hero">
  <div class="hero-photo" role="img" aria-label="Two smiling colleagues at a laptop in a bright office"></div>
  <div class="abs hero-copy">
    <h1>Welcome To<br>Velora</h1>
    <p>Excepteur sint occaecat cupidatat non proident, sunt in culpa &nbsp;deserunt mollit laborum.</p>
    <a class="btn" href="#">Get Started</a>
  </div>
  <svg class="abs hero-cut" viewBox="0 0 1200 120" preserveAspectRatio="none">
    <polygon points="0,0 0,120 1200,120 1200,0 820,80" fill="#ffffff"/>
    <polygon points="0,10 820,90 1200,0 1200,4 820,100 0,30" fill="#f26d21"/>
  </svg>
</section>

<section class="about">
  <div class="abs about-photo" role="img" aria-label="Team members discussing work at a computer">
    <svg width="426" height="387" viewBox="0 0 426 387"><polygon points="400,0 426,0 426,8 20,387 0,387 0,370" fill="#ffffff"/></svg>
  </div>
  <div class="abs about-body">
    <h2>About Velora<span class="caret"></span></h2>
    <p>Nemo enim ipsam voluptatem quia voluptas sit aspernatur aut odit aut fugit, sed quia consequuntur magni dolores eos qui ratione voluptatem sequi nesciunt. Neque porro quisquam est, qui dolorem ipsum quia dolor sit amet, consectetur, adipisci velit, sed quia non numquam eius modi tempora incidunt ut labore et dolore magnam aliquam quaerat voluptatem.</p>
    <p>Ut enim ad minima veniam,nisi ut aliquid ex ea commodi consequatur</p>
    <a class="btn" href="#">Read More</a>
  </div>
</section>

<section class="software">
  <svg class="abs software-bg" viewBox="0 0 1200 780" preserveAspectRatio="none"><polygon points="0,0 1200,52 1200,780 0,780" fill="#fdede3"/></svg>
  <h2 class="abs section-title">Our Software<span class="caret"></span></h2>
  <div class="abs tabs">
    <span class="tab active">Healthcare Organizations</span>
    <span class="tab" style="left:571px;top:12px">Sport Clubs</span>
    <span class="tab" style="left:792px;top:12px">Sport Hunting</span>
  </div>
  <div class="abs product" style="left:112px">
    <div class="product-photo" role="img" aria-label="Doctors reviewing scans on a monitor" style="background:linear-gradient(135deg,#9aa6b2,#5b6a78 50%,#c9b7a6)"></div>
    <div class="product-card"><h3>BlueHaven</h3><p>Quis autem vel eum iure reprehenderit in dolorem­que laudantium, totam rem aperiam, voluptate velit esse consequatur.</p></div>
    <a class="btn" href="#">Learn More</a>
  </div>
  <div class="abs product" style="left:450px">
    <div class="product-photo" role="img" aria-label="Fire crew standing in front of a red fire engine" style="background:linear-gradient(135deg,#4a4f57,#b3302e 55%,#6b6f75)"></div>
    <div class="product-card"><h3>Fire Brigade</h3><p>Sed ut perspiciatis unde omnis iste natus lore sit voluptatem accusantium doloue laudantium, lorem ipsum veritatis.</p></div>
    <a class="btn" href="#">Learn More</a>
  </div>
  <div class="abs product" style="left:788px">
    <div class="product-photo" role="img" aria-label="Pharmacist handing medicine to a customer" style="background:linear-gradient(135deg,#c9cfd6,#eef0f2 50%,#a9866e)"></div>
    <div class="product-card"><h3>Pharmacy</h3><p>Sed ut perspiciatis unde omnis iste natus lore sit voluptatem accusantium doloue laudantium, lorem ipsum veritatis.</p></div>
    <a class="btn" href="#">Learn More</a>
  </div>
</section>

<section class="testimonials">
  <h2 class="abs section-title">What Customers Says<span class="caret"></span></h2>
  <svg class="abs arrow" style="left:40px" width="26" height="20" viewBox="0 0 26 20"><path d="M25 10H3M11 2L3 10l8 8" stroke="#222" stroke-width="3" fill="none"/></svg>
  <svg class="abs arrow" style="left:1132px" width="26" height="20" viewBox="0 0 26 20"><path d="M1 10h22M15 2l8 8-8 8" stroke="#222" stroke-width="3" fill="none"/></svg>
  <div class="abs avatar" role="img" aria-label="Portrait of a customer in a grey suit"></div>
  <div class="abs quote-mark">“</div>
  <div class="abs testimonial-text">
    <h4>Excepteur sint occaecat cupidatat non proident,</h4>
    <p>Neque porro quisquam est, qui dolorem ipsum quia dolor sit amet, consectetur, adipisci velit, sed quia non numquam eius modi tempora incidunt ut labore et dolore magnam aliquam quaerat voluptatem.</p>
    <div class="who">Marten Alrik <small>(Manager)</small><span class="stars">★★★★★</span></div>
  </div>
</section>

<section class="news">
  <svg class="abs news-bg" width="1200" height="722" viewBox="0 0 1200 722" preserveAspectRatio="none"><polygon points="0,38 1200,0 1200,722 0,722" fill="#e8e8ea"/></svg>
  <h2 class="abs section-title">Latest News<span class="caret"></span></h2>
  <article class="abs post" style="left:108px">
    <div class="post-photo" role="img" aria-label="Team gathered around a laptop in an office" style="background:linear-gradient(135deg,#d7d3cc,#7b828c 60%,#3e4a5a)"></div>
    <div class="post-body"><div class="post-meta">Jan 19, 2022 &nbsp;| &nbsp;0 Comments</div><h3>Sed ut perspiciatis unde omnis iste natus</h3><p>Quis autem vel eum iure repre­herit qui in ea voluptate velit esse quam nihil molestiae &nbsp;fugiat vo­luptas nulla pariatur.</p><a href="#">- Learn More</a></div>
  </article>
  <article class="abs post" style="left:443px">
    <div class="post-photo" role="img" aria-label="Developers working at desktop computers" style="background:linear-gradient(135deg,#c8ccd1,#5f6670 55%,#2d3540)"></div>
    <div class="post-body"><div class="post-meta">Feb 2, 2022 &nbsp;| &nbsp;0 Comments</div><h3>Voluptatem accustium doloque laudtium</h3><p>Sed quia non numqum eius modi tempo incidunt ut labore et dolore magnam aliquam magni dolores totam rem apam quaerat volup.</p><a href="#">- Learn More</a></div>
  </article>
  <article class="abs post" style="left:779px">
    <div class="post-photo" role="img" aria-label="Two colleagues laughing at a computer" style="background:linear-gradient(135deg,#d9cfc3,#8f8a86 50%,#2f3845)"></div>
    <div class="post-body"><div class="post-meta">Jan 19, 2022 &nbsp;| &nbsp;0 Comments</div><h3>Nemo enim ipsam volu­tatem quia voluptas</h3><p>Duis aute irure dolor in repreh­derit in voluptate velit esse cillum dolore eu fugiat nulla pariaturi occaecat cupidatat lorem.</p><a href="#">- Learn More</a></div>
  </article>
</section>

<section class="contact">
  <h2 class="abs section-title">Get In Touch<span class="caret"></span></h2>
  <p class="abs contact-lead">Nemo enim ipsam voluptatem quia voluptas sit aspernatur aut odit aut fugit, sed quia consequuntur magni voluptatem sequi nesciunt.</p>
  <div class="abs info-card">
    <h2>CONTACT INFO</h2>
    <div class="info-row" style="top:160px">
      <span class="info-icon"><svg width="16" height="16" viewBox="0 0 24 24" fill="#fff"><path d="M12 2a7 7 0 00-7 7c0 5 7 13 7 13s7-8 7-13a7 7 0 00-7-7zm0 9.5A2.5 2.5 0 1112 6a2.5 2.5 0 010 5.5z"/></svg></span>
      <div><h4>ADDRESS</h4><p>Door No, 12 Harbor Lane<br>Westfield, US</p></div>
    </div>
    <div class="info-row" style="top:272px">
      <span class="info-icon"><svg width="16" height="16" viewBox="0 0 24 24" fill="#fff"><path d="M6.6 10.8a15 15 0 006.6 6.6l2.2-2.2c.3-.3.7-.4 1-.2 1.1.4 2.3.6 3.6.6.6 0 1 .4 1 1V20c0 .6-.4 1-1 1A17 17 0 013 4c0-.6.4-1 1-1h3.5c.6 0 1 .4 1 1 0 1.3.2 2.5.6 3.6.1.3 0 .7-.2 1z"/></svg></span>
      <div><h4>PHONE NO</h4><p>+1 555 014 2290</p></div>
    </div>
    <div class="info-row" style="top:364px">
      <span class="info-icon"><svg width="16" height="16" viewBox="0 0 24 24" fill="none" stroke="#fff" stroke-width="2"><rect x="3" y="5" width="18" height="14" rx="1"/><path d="M3 6l9 7 9-7"/></svg></span>
      <div><h4>EMAIL</h4><p>info@velora.com</p></div>
    </div>
  </div>
  <form class="abs message-form">
    <h2>SEND A MESSAGE</h2>
    <div class="field">Full Name</div>
    <div class="field">Phone no</div>
    <div class="field tall">Address</div>
    <div class="submit">SUBMIT</div>
  </form>
</section>

<footer class="site-footer">
  <svg class="abs footer-shape" width="1200" height="473" viewBox="0 0 1200 473" preserveAspectRatio="none">
    <polygon points="0,70 300,0 1200,70 1200,473 0,473" fill="#1f2127"/>
    <polygon points="0,70 300,0 90,70 0,110" fill="#f26d21"/>
    <polygon points="300,0 1200,60 1200,72 1000,58" fill="#f26d21"/>
  </svg>
  <div class="abs footer-col" style="left:110px">
    <h4>Contact</h4>
    <ul>
      <li><svg width="12" height="14" viewBox="0 0 24 24" fill="#fff" style="margin-top:7px"><path d="M12 2a7 7 0 00-7 7c0 5 7 13 7 13s7-8 7-13a7 7 0 00-7-7z"/></svg><span style="line-height:21px;margin-top:3px">xyz, Larkspur Street<br>Westfield, Oregon</span></li>
      <li style="margin-top:6px"><svg width="12" height="12" viewBox="0 0 24 24" fill="#fff" style="margin-top:8px"><path d="M6.6 10.8a15 15 0 006.6 6.6l2.2-2.2c.3-.3.7-.4 1-.2 1.1.4 2.3.6 3.6.6.6 0 1 .4 1 1V20c0 .6-.4 1-1 1A17 17 0 013 4c0-.6.4-1 1-1h3.5c.6 0 1 .4 1 1 0 1.3.2 2.5.6 3.6.1.3 0 .7-.2 1z"/></svg>+1 555 014 2290</li>
      <li style="margin-top:6px"><svg width="12" height="12" viewBox="0 0 24 24" fill="#fff" style="margin-top:8px"><rect x="2" y="5" width="20" height="14"/></svg>info@velora.com</li>
    </ul>
  </div>
  <div class="abs footer-col" style="left:397px">
    <h4>Quick Links</h4>
    <ul><li>→ Home</li><li>→ About</li><li>→ Our Software</li><li>→ Latest News</li><li>→ Contact</li></ul>
  </div>
  <div class="abs footer-col" style="left:650px">
    <h4>Help Center</h4>
    <ul><li>→ FAQ</li><li>→ Terms</li><li>→ Privacy Policy</li><li>→ Support Center</li><li>→ Conditions</li></ul>
  </div>
  <div class="abs footer-col" style="left:880px">
    <h4>About Velora</h4>
    <p class="lead">Excepteur sint occaecat cupidatat non proident, sunt in culpa qui officia deserunt</p>
    <p class="follow">FOLLOW US ON:</p>
    <div class="socials"><span></span><span></span><span></span><span></span></div>
  </div>
  <div class="abs footer-rule"></div>
  <p class="abs copyright">Copyrights@2022.Velora.All Rights Reserved</p>
</footer>

</body>
</html>
```